real esate business card with company logo and name

we need a business card design for a real esate company

The company name is Walsh & Brand Pty Ltd, and we have our logo designed and will upload. We want classic or moden feel. Black or white background. looks more textured. Should include folowinginformations
Owen Walsh and Lucy Brand
Sales Agents & Onsite Manager
p: 07 5948 2063
F: 07 5948 2174
M:0431 857 219
3/42 Marlow Crescent, FERNLEA QLD 4213

We want this business card looks professonal. Thank you in advance.

Industry/Entity Type

Real Estate Agent

Contact Information for Business Card

Owen Walsh and Lucy Brand
Onsite Manager & Sales Agents
p: 07 5948 2063
M:0431 857 219

Font styles to use
Serif

Colors
000000
fbfbfb
333333
959595

Requirements
Must have
• company logo and name, black or white back ground

```html
<!DOCTYPE html>
<html lang="en">
<head>
<meta charset="utf-8">
<title>Walsh &amp; Brand Pty Ltd — Business Cards</title>
<link rel="stylesheet" href="https://fonts.googleapis.com/css2?family=Marcellus+SC&family=Marcellus&display=swap">
<style>
  :root {
    --ink-black: #000000;
    --paper-white: #fbfbfb;
    --charcoal: #333333;
    --silver: #959595;
    --stage: #e4e4e4;
    --light-silver: #d6d6d6;
  }
  * { box-sizing: border-box; margin: 0; padding: 0; }
  html, body {
    width: 1200px;
    height: 913px;
    overflow: hidden;
  }
  body {
    background: var(--stage);
    position: relative;
    font-family: "Marcellus", Georgia, serif;
  }
  .card {
    position: absolute;
    top: 294px;
    width: 540px;
    height: 324px;
    overflow: hidden;
    box-shadow: 0 6px 18px rgba(0,0,0,0.18);
  }
  .card--front {
    left: 40px;
    background:
      linear-gradient(125deg, rgba(255,255,255,0.05) 0%, rgba(255,255,255,0.12) 38%, rgba(255,255,255,0.02) 52%, rgba(255,255,255,0) 100%),
      var(--ink-black);
    color: var(--paper-white);
  }
  .card--back {
    left: 620px;
    background: var(--paper-white);
  }

  /* Company mark area */
  .brand {
    position: absolute;
    display: flex;
    flex-direction: column;
    align-items: center;
  }
  .brand__square {
    width: 64px;
    height: 64px;
    background: var(--silver);
  }
  .brand__name {
    font-family: "Marcellus SC", Georgia, serif;
    letter-spacing: 0.08em;
    white-space: nowrap;
  }
  .card--front .brand {
    left: 24px;
    top: 112px;
    width: 190px;
  }
  .card--front .brand__name {
    margin-top: 18px;
    font-size: 12px;
    color: var(--silver);
  }

  .divider {
    position: absolute;
    left: 228px;
    top: 96px;
    width: 1px;
    height: 150px;
    background: var(--silver);
    opacity: 0.7;
  }

  .contact {
    position: absolute;
    left: 248px;
    top: 76px;
    right: 22px;
  }
  .contact__names {
    font-family: "Marcellus SC", Georgia, serif;
    font-size: 18px;
    letter-spacing: 0.02em;
    color: var(--paper-white);
    white-space: nowrap;
  }
  .contact__role {
    font-family: "Marcellus SC", Georgia, serif;
    font-size: 12px;
    color: var(--silver);
    margin-top: 2px;
    letter-spacing: 0.03em;
    white-space: nowrap;
  }
  .contact__address {
    margin-top: 22px;
    font-size: 12.5px;
    line-height: 1.45;
    color: var(--light-silver);
  }
  .contact__address .street { font-family: "Marcellus SC", Georgia, serif; }
  .contact__lines {
    list-style: none;
    margin-top: 10px;
    font-size: 12.5px;
    line-height: 1.75;
    color: var(--light-silver);
  }
  .contact__lines li {
    display: flex;
    align-items: center;
    gap: 8px;
  }
  .contact__lines svg {
    width: 11px;
    height: 11px;
    fill: var(--silver);
    flex: none;
  }

  /* Back of the card */
  .card--back .brand {
    left: 0;
    right: 0;
    top: 96px;
  }
  .card--back .brand__square {
    width: 96px;
    height: 96px;
  }
  .card--back .brand__name {
    margin-top: 34px;
    font-size: 17px;
    color: var(--charcoal);
    letter-spacing: 0.1em;
  }
</style>
</head>
<body>

  <section class="card card--front" aria-label="Business card front">
    <div class="brand">
      <span class="brand__square" aria-hidden="true"></span>
      <span class="brand__name">Walsh &amp; Brand Pty Ltd</span>
    </div>

    <span class="divider" aria-hidden="true"></span>

    <div class="contact">
      <p class="contact__names">Owen Walsh &amp; Lucy Brand</p>
      <p class="contact__role">Sales Agents &amp; Onsite Manager</p>
      <p class="contact__address">
        <span class="street">3/42 Marlow Crescent</span><br>
        FERNLEA QLD 4213
      </p>
      <ul class="contact__lines">
        <li>
          <svg viewBox="0 0 24 24" aria-label="Phone"><path d="M6.6 10.8a15.1 15.1 0 0 0 6.6 6.6l2.2-2.2c.3-.3.7-.4 1-.2 1.1.4 2.3.6 3.6.6.6 0 1 .4 1 1V20c0 .6-.4 1-1 1C10.6 21 3 13.4 3 4c0-.6.4-1 1-1h3.5c.6 0 1 .4 1 1 0 1.3.2 2.5.6 3.6.1.3 0 .7-.2 1z"/></svg>
          07 5948 2063
        </li>
        <li>
          <svg viewBox="0 0 24 24" aria-label="Fax"><path d="M6 3h10v5H6zM3 9h18v9h-3v3H6v-3H3zm5 6v4h8v-4z"/></svg>
          07 5948 2174
        </li>
        <li>
          <svg viewBox="0 0 24 24" aria-label="Mobile"><path d="M7 1h10a2 2 0 0 1 2 2v18a2 2 0 0 1-2 2H7a2 2 0 0 1-2-2V3a2 2 0 0 1 2-2zm0 3v14h10V4zm5 15.5a1.2 1.2 0 1 0 0 2.4 1.2 1.2 0 0 0 0-2.4z"/></svg>
          0431 857 219
        </li>
      </ul>
    </div>
  </section>

  <section class="card card--back" aria-label="Business card back">
    <div class="brand">
      <span class="brand__square" aria-hidden="true"></span>
      <span class="brand__name">Walsh &amp; Brand Pty Ltd</span>
    </div>
  </section>

</body>
</html>
```